New Business Card Design Project

We require a business card design for Vexalund, a newly established Indian company.
Our focus is on the development, manufacturing, and export of a diverse array of pharmaceutical products on a global scale. The card should convey a professional appearance, as our primary markets are in Africa, China, and Southeast Asian nations.
We envision a two-sided business card, with the reverse side dedicated to a logo set against a solid color or an elegantly designed pattern. The corners should be rounded. We would appreciate seeing both horizontal and vertical design options. We trust the designer to utilize their expertise in creating this design.

The content for the business card is included in the attached Word file.

Target Market(s)

Our primary markets are in Africa, China, and Southeast Asian, Latin America, Maldives, Sri Lanka

Industry/Entity Type

Pharmaceutical Manufacturing and Export

Contact Information for Business Card

Colors

Designer to choose colors to be used in the design.

Requirements
Must have
• The reverse side of the business card features solely the logo along with the tagline, "Care in Every Dose."
Should not have
• The logo should not exceed two instances, encompassing both the front and back sides of the card.

```html
<!DOCTYPE html>
<html lang="en">
<head>
<meta charset="utf-8">
<title>Vexalund Business Card</title>
<link rel="stylesheet" href="https://fonts.googleapis.com/css2?family=Open+Sans:wght@400;600;700&family=Poppins:wght@400&display=swap">
<style>
  :root {
    --stage: #232325;
    --brand-blue: #2fa8df;
    --coral: #f06550;
    --card-dark: #1f2024;
    --white: #ffffff;
    --soft-white: #e9ecef;
    --faint: rgba(47, 168, 223, 0.07);
  }
  * { margin: 0; padding: 0; box-sizing: border-box; }
  html, body {
    width: 1200px; height: 711px; overflow: hidden;
    background: var(--stage);
    font-family: "Open Sans", Arial, sans-serif;
  }
  .sheet {
    width: 1200px; height: 711px;
    display: flex; align-items: center; justify-content: center; gap: 40px;
  }
  .card {
    position: relative;
    width: 540px; height: 308px;
    border-radius: 22px;
    overflow: hidden;
  }
  /* Reverse side */
  .card--back {
    background: var(--brand-blue);
    display: flex; flex-direction: column; align-items: center; justify-content: center;
  }
  .brand {
    display: flex; align-items: center; gap: 14px;
  }
  .brand__dot {
    width: 30px; height: 30px; border-radius: 50%;
    background: var(--coral);
    flex: none;
  }
  .brand__name {
    font-family: "Open Sans", Arial, sans-serif;
    font-weight: 700;
    font-size: 56px;
    letter-spacing: 0.5px;
    color: var(--white);
    line-height: 1;
  }
  .tagline {
    margin-top: 18px;
    font-family: "Poppins", Arial, sans-serif;
    font-size: 14px;
    letter-spacing: 1px;
    color: var(--white);
  }
  /* Front side */
  .card--front {
    background: var(--card-dark);
    border-bottom: 3px solid var(--brand-blue);
  }
  .decor-circle {
    position: absolute;
    right: 30px; top: 40px;
    width: 210px; height: 210px; border-radius: 50%;
    background: var(--faint);
  }
  .front__brand {
    position: absolute; left: 34px; top: 40px;
    gap: 10px;
  }
  .front__brand .brand__dot { width: 20px; height: 20px; }
  .front__brand .brand__name {
    font-size: 38px;
    color: var(--brand-blue);
  }
  .address {
    position: absolute; left: 36px; top: 104px;
    font-size: 13px; line-height: 1.5;
    color: var(--soft-white);
    font-style: normal;
  }
  .contacts {
    position: absolute; left: 36px; bottom: 30px;
    list-style: none;
  }
  .contacts li {
    display: flex; align-items: center; gap: 10px;
    font-size: 13px; line-height: 1;
    color: var(--soft-white);
    margin-top: 9px;
  }
  .contacts svg { width: 15px; height: 15px; flex: none; }
  .person {
    position: absolute; right: 40px; top: 92px;
    text-align: right;
  }
  .person__name {
    font-size: 26px; line-height: 1.1;
    color: var(--brand-blue); font-weight: 700;
  }
  .person__name .person__surname {
    color: var(--coral); font-weight: 400;
  }
  .person__role {
    margin-top: 4px;
    font-size: 13px; color: var(--white);
  }
  .accent-bar {
    position: absolute; right: 0; top: 88px;
    width: 14px; height: 50px;
    background: var(--brand-blue);
  }
</style>
</head>
<body>
<main class="sheet">
  <section class="card card--back" aria-label="Card reverse side">
    <div class="brand">
      <span class="brand__dot"></span>
      <span class="brand__name">Vexalund</span>
    </div>
    <p class="tagline">Care in Every Dose.</p>
  </section>

  <section class="card card--front" aria-label="Card front side">
    <div class="decor-circle"></div>
    <div class="brand front__brand">
      <span class="brand__dot"></span>
      <span class="brand__name">Vexalund</span>
    </div>
    <address class="address">
      12, Nilgiri Nagar,<br>
      Wardha, 442001, India
    </address>
    <ul class="contacts">
      <li>
        <svg viewBox="0 0 16 16" aria-hidden="true"><rect x="3.5" y="1.5" width="9" height="13" rx="1.5" fill="none" stroke="#f06550" stroke-width="1.6"/><line x1="7" y1="12" x2="9" y2="12" stroke="#f06550" stroke-width="1.4"/></svg>
        +91 9876543210
      </li>
      <li>
        <svg viewBox="0 0 16 16" aria-hidden="true"><circle cx="8" cy="8" r="6.5" fill="none" stroke="#2fa8df" stroke-width="1.5"/><ellipse cx="8" cy="8" rx="2.8" ry="6.5" fill="none" stroke="#2fa8df" stroke-width="1.2"/><line x1="1.5" y1="8" x2="14.5" y2="8" stroke="#2fa8df" stroke-width="1.2"/></svg>
        www.vexalund.com
      </li>
      <li>
        <svg viewBox="0 0 16 16" aria-hidden="true"><rect x="1.5" y="3.5" width="13" height="9" rx="1" fill="none" stroke="#f06550" stroke-width="1.5"/><polyline points="1.5,4 8,9 14.5,4" fill="none" stroke="#f06550" stroke-width="1.5"/></svg>
        rvarde@vexalund.com
      </li>
    </ul>
    <div class="person">
      <p class="person__name">Rohan <span class="person__surname">K. Varde</span></p>
      <p class="person__role">CEO</p>
    </div>
    <div class="accent-bar"></div>
  </section>
</main>
</body>
</html>
```